BUSINESS CARD DESIGN

NAME- DALE VORSKIN
PHONE NUMER - 555- 714-9082
EMAIL- OFFICE@TRV-GROUNDMAKRZ.COM
BACK OF CARD- SPEACIALIZES IN LAND CLEARING, FORESTRY MUCLHING AND EXCAVATION

Contact Information for Business Card

NAME- DALE VORSKIN PHONE NUMER - 555- 714-9082 EMAIL- OFFICE@TRV-GROUNDMAKRZ.COM BACK OF CARD- SPEACIALIZES IN LAND CLEARING , MUCLHING AND EXCAVATION

```html
<!DOCTYPE html>
<html lang="en">
<head>
<meta charset="utf-8">
<title>Dale Vorskin — Business Card</title>
<link href="https://fonts.googleapis.com/css2?family=Grenze:wght@400;500;600&display=swap" rel="stylesheet">
<style>
  :root {
    --page: #e8e8e8;
    --card: #000000;
    --yellow: #fdc000;
    --teal: #1b8fa6;
    --steel: #2f6f86;
  }
  * { margin: 0; padding: 0; box-sizing: border-box; }
  html, body { width: 1200px; height: 1200px; overflow: hidden; }
  body {
    background: var(--page);
    font-family: "Grenze", Georgia, serif;
    position: relative;
  }
  .card {
    position: absolute;
    left: 281px;
    width: 589px;
    height: 337px;
    background: var(--card);
    overflow: hidden;
    box-shadow: 10px 14px 18px rgba(0,0,0,0.28);
  }
  .card--front { top: 52px; }
  .card--back { top: 405px; }

  .front__name {
    position: absolute;
    left: 38px;
    top: 28px;
    color: var(--yellow);
    font-weight: 600;
    font-size: 60px;
    line-height: 52px;
    letter-spacing: 0.5px;
  }
  .front__contact {
    position: absolute;
    left: 38px;
    top: 267px;
    list-style: none;
    color: var(--teal);
    font-size: 16px;
    line-height: 19px;
  }
  .front__contact li { display: flex; align-items: center; gap: 7px; }
  .front__contact svg { width: 13px; height: 13px; flex: none; }

  .front__illustration {
    position: absolute;
    left: 409px;
    top: 124px;
    width: 180px;
    height: 213px;
    background: linear-gradient(180deg, #d9a400 0%, #9a7a10 60%, #2f6f86 100%);
  }

  .back__stripes {
    position: absolute;
    left: 0;
    width: 100%;
    height: 24px;
  }
  .back__stripes--top { top: 0; }
  .back__stripes--bottom { bottom: 0; }

  .back__illustration {
    position: absolute;
    left: 185px;
    top: 24px;
    width: 254px;
    height: 289px;
    background: linear-gradient(180deg, rgba(253,192,0,0.16), rgba(47,111,134,0.14));
  }
  .back__tagline {
    position: absolute;
    left: 0;
    width: 100%;
    top: 124px;
    text-align: center;
    color: var(--yellow);
    font-weight: 500;
    font-size: 40px;
    line-height: 38px;
    letter-spacing: 0.3px;
  }
</style>
</head>
<body>
  <section class="card card--front">
    <h1 class="front__name">DALE<br>VORSKIN</h1>
    <ul class="front__contact">
      <li>
        <svg viewBox="0 0 16 16" aria-hidden="true">
          <circle cx="8" cy="8" r="8" fill="var(--teal)"/>
          <path d="M5 4.2c.4-.3.9-.2 1.1.2l.8 1.4c.2.4.1.8-.2 1l-.6.4c.5 1.1 1.3 1.9 2.4 2.4l.4-.6c.2-.3.7-.4 1-.2l1.4.8c.4.2.5.7.2 1.1-.7.9-1.7 1.2-2.7.7C6.9 10.6 5.4 9.1 4.6 7.2 4.1 6 4.3 5 5 4.2z" fill="#000"/>
        </svg>
        555 - 714 -9082
      </li>
      <li>
        <svg viewBox="0 0 16 16" aria-hidden="true">
          <rect x="1" y="3" width="14" height="10" fill="var(--teal)"/>
          <path d="M2.5 4.5 8 9l5.5-4.5" fill="none" stroke="#000" stroke-width="1.4"/>
        </svg>
        OFFICE@TRV-GROUNDMAKRZ.COM
      </li>
    </ul>
    <div class="front__illustration" role="img" aria-label="Illustration of a yellow tracked excavator with its bucket lowered onto a mound of earth"></div>
  </section>

  <section class="card card--back">
    <div class="back__illustration" role="img" aria-label="Faint background illustration of a tracked excavator"></div>
    <svg class="back__stripes back__stripes--top" viewBox="0 0 589 24" preserveAspectRatio="none" aria-hidden="true">
      <defs>
        <pattern id="hazard" width="43" height="24" patternUnits="userSpaceOnUse">
          <polygon points="0,24 16,0 42,0 26,24" fill="var(--yellow)"/>
        </pattern>
      </defs>
      <rect width="589" height="24" fill="url(#hazard)"/>
    </svg>
    <p class="back__tagline">Specialist In Land Clearing<br>Muchling &amp; Excavation</p>
    <svg class="back__stripes back__stripes--bottom" viewBox="0 0 589 24" preserveAspectRatio="none" aria-hidden="true">
      <rect width="589" height="24" fill="url(#hazard)"/>
    </svg>
  </section>
</body>
</html>
```